Bring me business with this creative business card

Design my new business card. I am looking for something different with an impact. People will take a look at this card & they will 1- see how different & creative I am, 2-understand what I do 3- Call me to meet me!

I make videos with a message, testimonials. I am dynamic, fun, creative & human. My new website is in construction but in the meantime you can check this old one: brightpath.ca & another one Tidebloom.com & tidebloom facebook page.
I make videos. sometimes with a cameraman, sometimes with my phone. As an ex Public Relations agent, the message is the most important thing for me. I want to make my clients shine! When they start with me they often remind me of a lamb, when I finish coaching them they are powerful like LIONS! That's why I need a powerful business card!

Target Market(s)

Entrepreneurs, solo entrepreneurs, small & medium companies & start ups. People i will meet while networking. People that need videos on their website & social Networks to get attention, to be visible. men & women. From 35 to 49 years old.
I am an ex Public relations agent. I used to send clients in traditional medias, now with videos they have more chances to be seen on google the new media. I do videos of the president, his team, his loyal clients saying how great the company is & expert videos like series so people can be seen for example every 1 st of every month with a short 2 minute video. Also with my 20 years in marketing & communications I can coach & give tips to anybody who needs it.
Target: anybody who would like my old website brightpath.ca & I also have another website but it will be off line soon: tidebloom.com could give you ideas.

Industry/Entity Type

Communications

Contact Information for Business Card

I am in Montreal,So the business cards have to be the usual size like we have in Montreal: 9 cm x 5 cm
Details:My text: Mathilde Tessier Communication coach/Chief Guide. "Crafting stories as bold as you" off: 514-555-0147 cell: 514-555-0183. tidebloom.com
mathilde@tidebloom.com logo facebook, youtube, instagram

Colors
f37122

Requirements
Must have
• Dynamic, happy. Orange. Be creative in the look but NOT the shape of the card. Easy to read. Big enough to read.
Should not have
• No funny shapes: no round, no square, just the usual. I love creative but NOT on shape.

```html
<!DOCTYPE html>
<html lang="en">
<head>
<meta charset="utf-8">
<title>Tidebloom Business Card</title>
<link rel="stylesheet" href="https://fonts.googleapis.com/css2?family=Cinzel:wght@700&family=Roboto+Condensed:wght@400;700&family=Roboto:wght@400;500&family=Ubuntu:wght@500&display=swap">
<style>
  :root {
    --page-bg: #3a3a3c;
    --card-bg: #252527;
    --brand-orange: #f37122;
    --brand-amber: #f6a21c;
    --ink-light: #f4f4f4;
    --rule-light: #d9d9d9;
  }
  * { box-sizing: border-box; margin: 0; padding: 0; }
  html, body {
    width: 1200px; height: 900px; overflow: hidden;
    background: var(--page-bg);
  }
  .canvas {
    position: relative; width: 1200px; height: 900px;
    display: flex; flex-direction: column; align-items: center; justify-content: center; gap: 30px;
  }
  .card {
    position: relative; width: 720px; height: 400px;
    background: var(--card-bg);
  }

  /* Front */
  .card-front {
    display: flex; flex-direction: column; align-items: center; padding-top: 44px;
  }
  .brand-mark {
    width: 124px; height: 124px; border-radius: 50%;
    background: var(--brand-amber);
  }
  .brand-name {
    margin-top: 18px;
    font-family: "Cinzel", serif; font-weight: 700; font-size: 46px; letter-spacing: 2px;
    color: var(--brand-orange); line-height: 1;
  }
  .brand-motto {
    display: flex; align-items: center; gap: 10px; margin-top: 8px;
    font-family: "Roboto Condensed", sans-serif; font-size: 17px; letter-spacing: 1px;
    color: var(--brand-amber);
  }
  .brand-motto::before, .brand-motto::after {
    content: ""; width: 40px; height: 2px; background: var(--brand-amber);
  }
  .brand-tagline {
    margin-top: 6px;
    font-family: "Ubuntu", sans-serif; font-weight: 500; font-size: 19px;
    color: var(--brand-orange);
  }
  .social-row {
    position: relative; width: 420px; margin-top: 18px;
    display: flex; justify-content: center; gap: 10px;
  }
  .social-row::before {
    content: ""; position: absolute; left: 0; right: 0; top: 50%; height: 1px;
    background: linear-gradient(90deg, transparent, var(--brand-orange) 30%, var(--brand-orange) 70%, transparent);
  }
  .social-dot {
    position: relative; width: 26px; height: 26px; border-radius: 50%;
    background: var(--brand-orange); border: 3px solid var(--card-bg);
  }

  /* Back */
  .card-back {
    display: flex; align-items: center; justify-content: center; gap: 34px;
  }
  .identity { text-align: right; }
  .person-name {
    font-family: "Roboto Condensed", sans-serif; font-weight: 700; font-size: 42px;
    color: var(--brand-orange); line-height: 1.05;
  }
  .person-role {
    font-family: "Roboto Condensed", sans-serif; font-size: 20px;
    color: var(--brand-amber); line-height: 1.2; text-transform: uppercase;
  }
  .divider {
    width: 2px; height: 120px;
    background: linear-gradient(180deg, transparent, var(--rule-light), transparent);
  }
  .contact-list { list-style: none; }
  .contact-item {
    display: flex; align-items: center; gap: 12px;
    font-family: "Roboto", sans-serif; font-size: 19px; color: var(--ink-light);
    line-height: 1.35;
  }
  .contact-icon { width: 16px; height: 16px; flex: none; fill: var(--brand-orange); }
</style>
</head>
<body>
<main class="canvas">
  <section class="card card-front">
    <div class="brand-mark" role="img" aria-label="Tidebloom brand emblem"></div>
    <h1 class="brand-name">TIDEBLOOM</h1>
    <p class="brand-motto">1 STORY 1 VOICE</p>
    <p class="brand-tagline">Crafting stories as bold as you</p>
    <div class="social-row" aria-label="Social profiles">
      <span class="social-dot"></span>
      <span class="social-dot"></span>
      <span class="social-dot"></span>
    </div>
  </section>

  <section class="card card-back">
    <div class="identity">
      <h2 class="person-name">MATHILDE T.</h2>
      <p class="person-role">Communication Coach</p>
      <p class="person-role">Chief Guide</p>
    </div>
    <div class="divider"></div>
    <ul class="contact-list">
      <li class="contact-item">
        <svg class="contact-icon" viewBox="0 0 16 16"><path d="M3.5 1.5l2.5 3-1.5 1.5c.8 1.8 2.2 3.2 4 4l1.5-1.5 3 2.5-1.5 2.5C6.5 13 3 9.5 1 4z"/></svg>
        <span>514-555-0147</span>
      </li>
      <li class="contact-item">
        <svg class="contact-icon" viewBox="0 0 16 16"><path d="M4 0h8a1 1 0 011 1v14a1 1 0 01-1 1H4a1 1 0 01-1-1V1a1 1 0 011-1zm1 2v10h6V2zm3 11a1 1 0 100 2 1 1 0 000-2z"/></svg>
        <span>514-555-0183.</span>
      </li>
      <li class="contact-item">
        <svg class="contact-icon" viewBox="0 0 16 16"><path d="M1 3h14v1.5L8 9 1 4.5zm0 3l7 4.5L15 6v7H1z"/></svg>
        <span>mathilde@tidebloom.com</span>
      </li>
      <li class="contact-item">
        <svg class="contact-icon" viewBox="0 0 16 16"><circle cx="8" cy="8" r="7"/><path d="M1 8h14M8 1c2.5 2 2.5 12 0 14M8 1c-2.5 2-2.5 12 0 14" stroke="#252527" stroke-width="1.2" fill="none"/></svg>
        <span>www.tidebloom.com</span>
      </li>
    </ul>
  </section>
</main>
</body>
</html>
```